Homeowners Insurance Provider Website

We are selling homeowners insurance policy / tenants Policy/Flood Insurance in USA in few states and planning expand nationally.

Our target audience are two folds: Customers (Buy policies) and Insurance Agents who wants to work with us to sell our policies to customers. But website should focus 80% on customers and 20% on agents. So, more customer focused user experience. Please note that there is no direct buy option for customers. They always go through insurance agents.

Customer focused, educational that makes buyer journey easy. We don’t want to come off as trying sell something as there is no direct sales involved from website.

Target Market(s)

Homeowners in USA and Insurance agent who sells these insurance.

Industry/Entity Type

Insurance

Number of Pages Required

4 page

Font styles to use
Other font styles liked:
• Open to suggestions

Colors

Designer to choose colors to be used in the design.

Requirements
Must have
• Three most important things: Trustworthy, Authentic, Simple
• Please use colors form logo and grays
• We like: www.hollowmere.com
• https://www.quillfenbrook.com/
• We need Agent Look up tool on home page similar to what is shown on example sites.
• Design:
• Home Page - Open to Ideas
• Insurance (Products) Landing Page - Info similar to: https://www.quillfenbrook.com/insurance/
• Agents Page - https://www.quillfenbrook.com/agents/
• Claims Page - Information similar to: https://www.quillfenbrook.com/claims-center/
• Site Navigation:
• Home
• Insurance
• Claims
• Agents
• About Us
• Contact Us
Nice to have
• Elegant, minimal and clean design that reflects trust and authenticity.
Should not have
• Slider or rotating images - prefer flat design. Not over powering design.

```html
<!DOCTYPE html>
<html lang="en">
<head>
<meta charset="utf-8">
<title>Hearthline Insurance Co. — Find an Agent</title>
<link rel="stylesheet" href="https://fonts.googleapis.com/css2?family=Montserrat:wght@500;600;700;800&family=Open+Sans:wght@400;600;700&display=swap">
<style>
:root{
  --red:#d3202f;
  --navy:#1f3a7a;
  --navy-deep:#1c3472;
  --ink:#333;
  --muted:#777;
  --gray-bg:#f2f2f2;
  --line:#e3e3e3;
  --white:#fff;
}
*{box-sizing:border-box;margin:0;padding:0}
html,body{width:1200px;height:3475px;overflow:hidden}
body{font-family:"Open Sans",Arial,sans-serif;color:var(--ink);background:var(--white);position:relative}
section,header,footer,div{position:relative}
.btn{display:inline-block;background:var(--red);color:var(--white);font-family:"Open Sans",Arial,sans-serif;font-size:22px;letter-spacing:.5px;padding:12px 28px;text-transform:uppercase}
h2.title{font-family:"Montserrat",Arial,sans-serif;font-weight:800;font-size:38px;text-transform:uppercase;letter-spacing:.5px;color:var(--navy)}
h2.title .accent{color:var(--red)}
p.lead{font-size:14px;line-height:23px;color:var(--muted)}

/* top bar */
.topbar{height:51px;background:var(--red);color:var(--white);display:flex;align-items:center;padding:0 78px;justify-content:space-between}
.social{display:flex;gap:14px}
.social span{width:14px;height:14px;border-radius:50%;background:rgba(255,255,255,.85)}
.topbar-right{display:flex;align-items:center;gap:36px;font-size:17px}
.phone{display:flex;align-items:center;gap:12px;font-weight:700;font-size:20px}

/* nav */
.nav{height:83px;display:flex;align-items:center;justify-content:space-between;padding:0 78px;border-bottom:1px solid var(--line)}
.nav ul{list-style:none;display:flex;gap:40px;font-family:"Montserrat",Arial,sans-serif;font-weight:600;font-size:17px;color:var(--navy)}
.nav li.active{color:var(--red)}
.brand{display:flex;align-items:center;gap:14px;position:absolute;left:50%;transform:translateX(-50%);top:14px}
.brand-mark{width:52px;height:52px;background:var(--navy)}
.brand-name{font-family:"Montserrat",Arial,sans-serif;font-weight:700;font-size:24px;line-height:28px;color:var(--navy);text-transform:uppercase;width:230px}

/* hero */
.hero{height:519px;text-align:center;color:var(--white);padding-top:137px;overflow:hidden}
.hero-photo{position:absolute;inset:0;background:linear-gradient(100deg,#5d6266 0%,#3a3e42 45%,#2b2e31 70%,#55595c 100%)}
.hero-content{position:relative}
.hero h1{font-family:"Montserrat",Arial,sans-serif;font-weight:700;font-size:70px;letter-spacing:1px}
.hero p{font-size:18px;line-height:26px;width:900px;margin:8px auto 26px}
.btn-light{display:inline-block;background:var(--white);color:#222;font-size:22px;padding:14px 36px}

/* welcome */
.welcome{height:315px;background:var(--gray-bg);text-align:center;padding-top:52px}
.welcome p.lead{width:870px;margin:16px auto 20px}

/* agents intro */
.agents-intro{height:450px;background:var(--white);overflow:hidden}
.agents-intro-photo{position:absolute;left:695px;top:0;width:505px;height:450px;background:linear-gradient(90deg,#f4f6f7 0%,#dfe6e9 40%,#c9d3d8 100%)}
.agents-intro-text{position:absolute;left:79px;top:86px;width:490px}
.agents-intro-text p.lead{margin:12px 0 22px;color:#555}

/* products */
.products{height:440px;background:var(--gray-bg);text-align:center;padding-top:50px}
.product-grid{display:flex;justify-content:center;gap:0;margin-top:28px}
.product{width:265px}
.product svg{display:block;margin:0 auto}
.product h3{font-family:"Montserrat",Arial,sans-serif;font-weight:700;font-size:21px;color:var(--navy);margin:14px 0 8px}
.product p{font-size:13px;line-height:20px;color:var(--muted);width:240px;margin:0 auto}

/* agents */
.agents{height:487px;background:var(--white);text-align:center;padding-top:52px}
.agents h2.title{color:var(--red)}
.agent-row{display:flex;justify-content:center;gap:14px;margin-top:38px}
.agent{width:250px}
.agent-photo{width:106px;height:106px;border-radius:50%;border:3px solid var(--navy);margin:0 auto;background:radial-gradient(circle at 50% 40%,#d9c2ad 0%,#b9a18b 45%,#eef0f2 46%,#e6e8ea 100%)}
.agent h3{font-family:"Montserrat",Arial,sans-serif;font-weight:700;font-size:21px;color:var(--navy);margin:10px 0 14px}
.agent-card{border:1px solid var(--line);box-shadow:0 2px 6px rgba(0,0,0,.08);padding:14px 12px 12px;height:134px}
.agent-card p{font-size:13px;line-height:20px;color:var(--muted)}
.agent-card a{display:inline-block;margin-top:6px;font-size:13px;font-weight:700;color:var(--red);text-decoration:underline}
.arrow{position:absolute;top:250px}

/* faq */
.faq{height:517px;background:var(--gray-bg);padding-top:48px}
.faq h2.title{text-align:center;text-transform:none;font-size:40px}
.faq-list{width:813px;margin:22px auto 0}
.faq-item{background:var(--white);box-shadow:0 1px 4px rgba(0,0,0,.08);margin-bottom:8px;padding:16px 24px;display:flex;justify-content:space-between;align-items:center;font-family:"Montserrat",Arial,sans-serif;font-weight:700;font-size:17px;color:var(--navy)}
.faq-item .toggle{color:var(--red);font-size:26px;font-weight:500;line-height:18px}
.faq-item.open{display:block;padding-bottom:18px}
.faq-q{display:flex;justify-content:space-between;align-items:center}
.faq-a{display:flex;justify-content:space-between;align-items:flex-end;margin-top:14px;gap:22px}
.faq-a p{font-family:"Open Sans",Arial,sans-serif;font-weight:400;font-size:13px;line-height:20px;color:#999}
.faq-a .btn{font-size:20px;padding:8px 24px;white-space:nowrap}

/* career */
.career{height:317px;background:var(--white)}
.career-photo{position:absolute;left:0;top:0;width:463px;height:317px;background:linear-gradient(180deg,#ffffff 0%,#e9e4e1 50%,#2b2b30 100%)}
.career-text{position:absolute;left:514px;top:62px;width:620px}
.career-text p.lead{color:#555;margin:12px 0 26px}

/* footer */
.footer{height:243px;background:var(--navy-deep);color:var(--white);display:flex;padding:38px 0 0 79px}
.footer h4{font-family:"Montserrat",Arial,sans-serif;font-weight:600;font-size:21px;margin-bottom:22px}
.col-contact{width:357px}
.contact-line{display:flex;gap:16px;font-size:14px;line-height:20px;margin-bottom:14px;align-items:flex-start}
.col-news{width:375px}
.news-item{display:flex;gap:14px;margin-bottom:12px}
.news-thumb{width:52px;height:52px;border-radius:50%;background:linear-gradient(135deg,#c4cad3,#7d8aa3);flex:none}
.news-item p{font-size:14px;line-height:19px}
.news-item small{display:block;font-size:12px;margin-top:3px;color:#d5dcea}
.col-letter p{font-size:14px;line-height:21px;width:280px}
.signup{display:flex;margin-top:22px;width:330px;height:52px}
.signup span{flex:1;background:var(--white);color:#8a8a8a;font-style:italic;font-size:15px;padding:15px 16px}
.signup b{width:56px;background:var(--red);display:flex;align-items:center;justify-content:center}

.legal{height:53px;background:var(--red);color:var(--white);display:flex;justify-content:space-between;align-items:center;padding:0 79px;font-size:14px}
.legal strong{font-weight:700}
.legal nav{display:flex;gap:12px}
</style>
</head>
<body>

<header>
  <div class="topbar">
    <div class="social"><span></span><span></span><span></span><span></span></div>
    <div class="topbar-right">
      <span>LOGIN</span>
      <span class="phone">
        <svg width="14" height="24" viewBox="0 0 14 24"><rect x="1" y="1" width="12" height="22" rx="2" fill="none" stroke="#fff" stroke-width="2"/><rect x="5" y="18" width="4" height="2" fill="#fff"/></svg>
        123 456 7878
      </span>
    </div>
  </div>
  <nav class="nav">
    <ul><li class="active">Home</li><li>About Us</li><li>Insurance</li></ul>
    <div class="brand"><span class="brand-mark"></span><span class="brand-name">Hearthline Insurance Co.</span></div>
    <ul><li>Agents</li><li>Claims</li><li>Contact Us</li></ul>
  </nav>
</header>

<section class="hero">
  <div class="hero-photo" role="img" aria-label="Dark photo of a person working at a laptop with financial charts overlaid"></div>
  <div class="hero-content">
    <h1>FIND AN AGENT</h1>
    <p>Lorem Ipsum is simply dummy text of the printing and typesetting industry. Lorem Ipsum has been the industry's standard dummy text ever since the 1500</p>
    <span class="btn-light">LEARN MORE</span>
  </div>
</section>

<section class="welcome">
  <h2 class="title"><span class="accent">Welcome to</span> Hearthline Insurance Co.</h2>
  <p class="lead">Lorem Ipsum is simply dummy text of the printing and typesetting industry. Lorem Ipsum has been the industry's standard dummy text ever since the 1500s, when an unknown printer took a galley of type and scrambled it to make a type specimen book. It has survived not only five centuries, but also the leap into electronic typesetting, remaining essentially unchanged. It was popularised in the 1960s with the release of Letraset sheets containing Lorem Ipsum passages.</p>
  <span class="btn">Learn More</span>
</section>

<section class="agents-intro">
  <div class="agents-intro-photo" role="img" aria-label="Photo of an insurance agent on the phone working at a laptop by a bright window"></div>
  <div class="agents-intro-text">
    <h2 class="title"><span class="accent">Insurance</span> Agents</h2>
    <p class="lead">Lorem Ipsum is simply dummy text of the printing and typesetting industry. Lorem Ipsum has been the industry's standard dummy text ever since the 1500s, when an unknown printer took a galley of type and scrambled it to make a type specimen book. It has survived not only five centuries, but also the leap into electronic typesetting, remaining essentially unchanged. It was popularised in the 1960s with the release of Letraset sheets containing Lorem Ipsum passages.</p>
    <span class="btn">Get Started Now</span>
  </div>
</section>

<section class="products">
  <h2 class="title"><span class="accent">Welcome to</span> Hearthline Insurance Co.</h2>
  <div class="product-grid">
    <div class="product">
      <svg width="100" height="160" viewBox="0 0 100 160"><path d="M50 3 L96 26 V104 L50 156 L4 104 V26 Z" fill="#fff" stroke="#1f3a7a" stroke-width="4"/><path d="M24 68 L50 44 L76 68 H68 V96 H32 V68 Z" fill="#d3202f"/><rect x="44" y="78" width="12" height="18" fill="#fff"/></svg>
      <h3>Homeowners</h3>
      <p>Lorem Ipsum is simply dummy text of the printing and typesetting industry. Lorem Ipsum has been dummy text.</p>
    </div>
    <div class="product">
      <svg width="100" height="160" viewBox="0 0 100 160"><path d="M50 3 L96 26 V104 L50 156 L4 104 V26 Z" fill="#fff" stroke="#1f3a7a" stroke-width="4"/><rect x="34" y="46" width="32" height="52" fill="#d3202f"/><rect x="22" y="64" width="12" height="34" fill="#d3202f"/><rect x="66" y="64" width="12" height="34" fill="#d3202f"/><g fill="#fff"><rect x="39" y="52" width="6" height="6"/><rect x="55" y="52" width="6" height="6"/><rect x="39" y="64" width="6" height="6"/><rect x="55" y="64" width="6" height="6"/><rect x="39" y="76" width="6" height="6"/><rect x="55" y="76" width="6" height="6"/><rect x="46" y="88" width="8" height="10"/></g></svg>
      <h3>Renters/Condo</h3>
      <p>Lorem Ipsum is simply dummy text of the printing and typesetting industry. Lorem Ipsum has been dummy text.</p>
    </div>
    <div class="product">
      <svg width="100" height="160" viewBox="0 0 100 160"><path d="M50 3 L96 26 V104 L50 156 L4 104 V26 Z" fill="#fff" stroke="#1f3a7a" stroke-width="4"/><path d="M22 70 L50 46 L78 70 V98 H22 Z" fill="#d3202f"/><path d="M50 94 C38 94 36 82 42 74 C44 80 47 80 48 76 C48 68 54 64 56 60 C58 70 66 74 62 86 C60 92 56 94 50 94 Z" fill="#fff"/></svg>
      <h3>Dwelling Fire</h3>
      <p>Lorem Ipsum is simply dummy text of the printing and typesetting industry. Lorem Ipsum has been dummy text.</p>
    </div>
    <div class="product">
      <svg width="100" height="160" viewBox="0 0 100 160"><path d="M50 3 L96 26 V104 L50 156 L4 104 V26 Z" fill="#fff" stroke="#1f3a7a" stroke-width="4"/><path d="M50 98 C40 84 32 74 32 62 A18 18 0 0 1 68 62 C68 74 60 84 50 98 Z" fill="none" stroke="#d3202f" stroke-width="4"/><circle cx="50" cy="61" r="7" fill="none" stroke="#d3202f" stroke-width="4"/></svg>
      <h3>Agent Locator</h3>
      <p>Lorem Ipsum is simply dummy text of the printing and typesetting industry. Lorem Ipsum has been dummy text.</p>
    </div>
  </div>
</section>

<section class="agents">
  <h2 class="title">Agents</h2>
  <svg class="arrow" style="left:136px" width="16" height="32" viewBox="0 0 16 32"><path d="M14 2 L2 16 L14 30" fill="none" stroke="#ccc" stroke-width="2"/></svg>
  <svg class="arrow" style="left:1050px" width="16" height="32" viewBox="0 0 16 32"><path d="M2 2 L14 16 L2 30" fill="none" stroke="#d3202f" stroke-width="2"/></svg>
  <div class="agent-row">
    <div class="agent">
      <div class="agent-photo" role="img" aria-label="Portrait photo of an agent"></div>
      <h3>Lorem ipsum</h3>
      <div class="agent-card"><p>Lorem Ipsum is simply dummy text of the printing and typesetting industry. Lorem Ipsum has been the industry's standard text.</p><a>VIEW FULL PROFILE</a></div>
    </div>
    <div class="agent">
      <div class="agent-photo" role="img" aria-label="Portrait photo of an agent"></div>
      <h3>Lorem ipsum</h3>
      <div class="agent-card"><p>Lorem Ipsum is simply dummy text of the printing and typesetting industry. Lorem Ipsum has been the industry's standard text.</p><a>VIEW FULL PROFILE</a></div>
    </div>
    <div class="agent">
      <div class="agent-photo" role="img" aria-label="Portrait photo of an agent"></div>
      <h3>Lorem ipsum</h3>
      <div class="agent-card"><p>Lorem Ipsum is simply dummy text of the printing and typesetting industry. Lorem Ipsum has been the industry's standard text.</p><a>VIEW FULL PROFILE</a></div>
    </div>
  </div>
</section>

<section class="faq">
  <h2 class="title">FAQ's</h2>
  <div class="faq-list">
    <div class="faq-item open">
      <div class="faq-q"><span>1. Lorem Ipsum is simply dummy text of the printing industry?</span><span class="toggle">–</span></div>
      <div class="faq-a">
        <p>Lorem Ipsum is simply dummy text of the printing and typesetting industry. Lorem Ipsum has been the industry's standard dummy text ever since the 1500s, when an unknown printer took a galley of type and scrambled it to make a type specimen book. It has survived not only five centuries, but also the leap into electronic typesetting, remaining essentially unchanged.</p>
        <span class="btn">More &nbsp;&gt;</span>
      </div>
    </div>
    <div class="faq-item"><span>2. Lorem Ipsum is simply dummy text of the printing and typesetting industry?</span><span class="toggle">+</span></div>
    <div class="faq-item"><span>3. Lorem Ipsum is simply dummy text ?</span><span class="toggle">+</span></div>
    <div class="faq-item"><span>4. Lorem Ipsum is simply dummy text of the printing industry?</span><span class="toggle">+</span></div>
  </div>
</section>

<section class="career">
  <div class="career-photo" role="img" aria-label="Photo of a smiling team of business professionals"></div>
  <div class="career-text">
    <h2 class="title">Career</h2>
    <p class="lead">Lorem Ipsum is simply dummy text of the printing and typesetting industry. Lorem Ipsum has been the industry's standard dummy text ever since the 1500s, when an unknown printer took a galley of type and scrambled it to make a type specimen book.</p>
    <span class="btn">Get Started Now</span>
  </div>
</section>

<footer>
  <div class="footer">
    <div class="col-contact">
      <h4>Contact Info</h4>
      <div class="contact-line">
        <svg width="20" height="26" viewBox="0 0 20 26"><path d="M10 24 C4 16 2 12 2 9 A8 8 0 0 1 18 9 C18 12 16 16 10 24 Z" fill="none" stroke="#fff" stroke-width="1.8"/><circle cx="10" cy="9" r="3" fill="none" stroke="#fff" stroke-width="1.8"/></svg>
        <span>123,Lorem ipsum dummy text,<br>Country-123456</span>
      </div>
      <div class="contact-line">
        <svg width="20" height="20" viewBox="0 0 20 20"><path d="M4 2 L8 2 L9 6 L7 8 C8 11 9 12 12 13 L14 11 L18 12 L18 16 C18 17 17 18 16 18 C9 18 2 11 2 4 C2 3 3 2 4 2 Z" fill="none" stroke="#fff" stroke-width="1.6"/></svg>
        <span>818-555-0134</span>
      </div>
      <div class="contact-line">
        <svg width="20" height="16" viewBox="0 0 20 16"><rect x="1" y="1" width="18" height="14" fill="none" stroke="#fff" stroke-width="1.6"/><path d="M1 1 L10 9 L19 1" fill="none" stroke="#fff" stroke-width="1.6"/></svg>
        <span>info@hearthlineinsurance.com</span>
      </div>
    </div>
    <div class="col-news">
      <h4>Latest News Posts</h4>
      <div class="news-item"><span class="news-thumb" role="img" aria-label="News post thumbnail photo"></span><p>Lorem Ipsum is simply dummy text of the printing and typesetting industry.<small>Feb 2, 2018</small></p></div>
      <div class="news-item"><span class="news-thumb" role="img" aria-label="News post thumbnail photo"></span><p>Lorem Ipsum is simply dummy text of the printing and typesetting industry.<small>Feb 2, 2018</small></p></div>
    </div>
    <div class="col-letter">
      <h4>Newsletter</h4>
      <p>Sign up to get Latest News &amp; Updates of Larkspur Builders</p>
      <div class="signup"><span>Type Here...</span><b><svg width="24" height="18" viewBox="0 0 24 18"><rect x="1" y="1" width="22" height="16" fill="none" stroke="#fff" stroke-width="2"/><path d="M1 1 L12 10 L23 1" fill="none" stroke="#fff" stroke-width="2"/></svg></b></div>
    </div>
  </div>
  <div class="legal">
    <span>© <strong>HEARTHLINE INSURANCE CO.</strong> - 2018. All Rights Reserved.</span>
    <nav><span>Home</span>|<span>Support</span>|<span>Press</span>|<span>Privacy Policy</span>|<span>Sitemap</span></nav>
  </div>
</footer>

</body>
</html>
```